Kestrel Facilities Business Card Design

We would now like to design business cards with the new Kestrel Facilities logo

Target Market(s)

Professional

Industry/Entity Type

Professional services

Contact Information for Business Card

Employee name, title, phone number, email address, corporate office address and logo.

Font styles to use
Sans Serif

Colors
0054AA
0677BA
7BADD7
CADEEF
E8F1F8

Requirements
Must have
• My logo
Should not have
• any other pictures or images besides my logo

```html
<!DOCTYPE html>
<html lang="en">
<head>
<meta charset="utf-8">
<title>Kestrel Facilities Business Card</title>
<link rel="stylesheet" href="https://fonts.googleapis.com/css2?family=Montserrat:wght@400;500;700&display=swap">
<style>
  :root {
    --brand-blue: #3378c1;
    --brand-deep: #0054aa;
    --brand-mid: #0677ba;
    --brand-soft: #7badd7;
    --brand-pale: #cadeef;
    --paper: #ffffff;
    --swoosh-grey: #a3a5a8;
    --stage: #2f3237;
  }
  * { box-sizing: border-box; margin: 0; padding: 0; }
  html, body {
    width: 1200px; height: 1012px; overflow: hidden;
    background: var(--stage);
    font-family: "Montserrat", sans-serif;
  }
  .card-sheet {
    width: 1200px; height: 1012px;
    display: flex; flex-direction: column;
    align-items: center; justify-content: center; gap: 40px;
  }
  .card {
    position: relative;
    width: 760px; height: 434px;
    overflow: hidden;
    box-shadow: 0 10px 30px rgba(0,0,0,.45);
  }
  /* Back */
  .card-back { background: var(--brand-blue); }
  .back-pattern {
    position: absolute; inset: 0;
    background: linear-gradient(135deg, #3a80c8 0%, #3173bb 100%);
  }
  .back-brand {
    position: absolute; left: 50%; top: 50%;
    transform: translate(-50%, -50%);
    display: flex; align-items: center; gap: 10px;
    color: var(--paper); font-weight: 500; font-size: 18px; letter-spacing: .04em;
  }
  .brand-square {
    width: 22px; height: 22px; border: 3px solid currentColor;
  }
  /* Front */
  .card-front { background: var(--paper); }
  .front-waves { position: absolute; inset: 0; width: 100%; height: 100%; }
  .front-brand {
    position: absolute; right: 48px; top: 66px;
    display: flex; align-items: center; gap: 14px;
    color: var(--brand-blue); font-weight: 500; font-size: 30px; letter-spacing: .03em;
  }
  .front-brand .brand-square { width: 40px; height: 40px; border-width: 5px; }
  .contact {
    position: absolute; left: 62px; top: 244px;
    color: var(--paper);
  }
  .contact-name { font-weight: 700; font-size: 25px; letter-spacing: .01em; line-height: 1.2; }
  .contact-title { font-weight: 400; font-size: 17px; margin: 2px 0 0 18px; }
  .contact-address { font-size: 16px; line-height: 1.3; margin: 12px 0 0 40px; }
  .contact-lines { list-style: none; font-size: 16px; line-height: 1.35; margin: 8px 0 0 40px; }
  .contact-lines li { display: flex; align-items: center; gap: 8px; }
  .contact-lines svg { width: 15px; height: 15px; fill: var(--paper); }
</style>
</head>
<body>
<main class="card-sheet">
  <section class="card card-back" aria-label="Card back">
    <div class="back-pattern" role="img" aria-label="Repeating brand-mark pattern in soft blue tones"></div>
    <div class="back-brand"><span class="brand-square"></span>Kestrel Facilities</div>
  </section>

  <section class="card card-front" aria-label="Card front">
    <svg class="front-waves" viewBox="0 0 1050 600" preserveAspectRatio="none" aria-hidden="true">
      <path d="M0 272 C 300 190, 650 240, 1050 180 L1050 600 L0 600 Z" fill="var(--swoosh-grey)"/>
      <path d="M0 294 C 300 212, 650 262, 1050 202 L1050 600 L0 600 Z" fill="var(--paper)"/>
      <path d="M0 300 C 300 218, 650 268, 1050 208 L1050 600 L0 600 Z" fill="var(--brand-soft)"/>
      <path d="M0 312 C 300 230, 650 280, 1050 220 L1050 600 L0 600 Z" fill="var(--brand-blue)"/>
    </svg>

    <div class="front-brand"><span class="brand-square"></span>Kestrel Facilities</div>

    <div class="contact">
      <p class="contact-name">DARA WHITFIELD</p>
      <p class="contact-title">Co-Founder</p>
      <p class="contact-address">418 Alder Park Lane<br>Suite 210 Brookvale 44</p>
      <ul class="contact-lines">
        <li>
          <svg viewBox="0 0 24 24" aria-hidden="true"><path d="M6.6 10.8a15.1 15.1 0 0 0 6.6 6.6l2.2-2.2a1 1 0 0 1 1-.25 11.4 11.4 0 0 0 3.6.57 1 1 0 0 1 1 1V20a1 1 0 0 1-1 1A17 17 0 0 1 3 4a1 1 0 0 1 1-1h3.5a1 1 0 0 1 1 1c0 1.25.2 2.450.57 3.57a1 1 0 0 1-.25 1z"/></svg>
          +1-555-014-2290
        </li>
        <li>
          <svg viewBox="0 0 24 24" aria-hidden="true"><path d="M2 5h20v14H2z M2 5l10 8 10-8" fill="var(--paper)" stroke="var(--brand-blue)" stroke-width="1.5"/></svg>
          hello@kestrelfac.com
        </li>
      </ul>
    </div>
  </section>
</main>
</body>
</html>
```